Im open to ideas.. I was thinking on my business cards aswell as my logo. a place for my name. email. phone number and abn..

ive attched a file with my business logo. which i dont love the colours.. i was think a dark background with charcoal letters so something along those colour schumes but im open to ideas..

BRM Constructions

```html
<!DOCTYPE html>
<html lang="en">
<head>
<meta charset="utf-8">
<title>BRM Constructions – Business Card</title>
<link rel="stylesheet" href="https://fonts.googleapis.com/css2?family=Open+Sans:wght@400;600;700&display=swap">
<style>
  :root {
    --backdrop: #3b3430;
    --card: #1b1b1b;
    --card-edge: #262626;
    --silver: #c4c4c4;
    --text-light: #e6e6e6;
    --text-muted: #b5b5b5;
  }
  * { margin: 0; padding: 0; box-sizing: border-box; }
  html, body {
    width: 1200px;
    height: 844px;
    overflow: hidden;
    background: var(--backdrop);
    font-family: "Open Sans", Arial, sans-serif;
  }
  .stage {
    position: relative;
    width: 1200px;
    height: 844px;
  }
  .card {
    position: absolute;
    top: 272px;
    width: 525px;
    height: 300px;
    background: var(--card);
    border: 1px solid var(--card-edge);
    border-radius: 3px;
  }
  .card--contact { left: 50px; }
  .card--brand { left: 625px; }

  .contact-brand {
    position: absolute;
    top: 48px;
    right: 44px;
    font-size: 26px;
    font-weight: 700;
    color: var(--silver);
    letter-spacing: 0.5px;
  }
  .contact-details {
    position: absolute;
    left: 40px;
    bottom: 36px;
    color: var(--text-light);
  }
  .person-name {
    font-size: 19px;
    font-weight: 600;
    line-height: 1.1;
  }
  .person-role {
    font-size: 14px;
    color: var(--text-muted);
    margin-bottom: 18px;
  }
  .abn {
    font-size: 14px;
    font-weight: 700;
    margin-bottom: 14px;
  }
  .contact-list { list-style: none; }
  .contact-list li {
    display: flex;
    align-items: center;
    gap: 10px;
    font-size: 15px;
    line-height: 22px;
  }
  .contact-list svg { width: 12px; height: 12px; fill: var(--text-muted); flex: none; }

  .brand-name {
    position: absolute;
    inset: 0;
    display: flex;
    align-items: center;
    justify-content: center;
    font-size: 44px;
    font-weight: 700;
    color: var(--silver);
    letter-spacing: 1px;
  }
</style>
</head>
<body>
<main class="stage">
  <section class="card card--contact" aria-label="Business card, contact side">
    <div class="contact-brand">BRM Constructions</div>
    <div class="contact-details">
      <p class="person-name">Daniel Hart</p>
      <p class="person-role">Managing Director</p>
      <p class="abn">ABN NO: 12345</p>
      <ul class="contact-list">
        <li>
          <svg viewBox="0 0 12 12" aria-hidden="true"><path d="M2.5 0.5 L4.5 3 L3.4 4.3 C4.1 5.8 6.2 7.9 7.7 8.6 L9 7.5 L11.5 9.5 L10.2 11.3 C5.8 11.3 0.7 6.2 0.7 1.8 Z"/></svg>
          (044)-456-7890
        </li>
        <li>
          <svg viewBox="0 0 12 12" aria-hidden="true"><path d="M0.5 2.5 H11.5 V9.5 H0.5 Z M1.2 3 L6 6.6 L10.8 3 Z" fill-rule="evenodd"/></svg>
          info@youremail.com
        </li>
        <li>
          <svg viewBox="0 0 12 12" aria-hidden="true"><circle cx="6" cy="6" r="5.5"/></svg>
          www.website.com
        </li>
      </ul>
    </div>
  </section>

  <section class="card card--brand" aria-label="Business card, brand side">
    <div class="brand-name">BRM Constructions</div>
  </section>
</main>
</body>
</html>
```